Harbourline Physiotherapy business card design

We need a fresh, new business card design for our physiotherapy clinic Harbourline Physiotherapy

Will attach logo soon we had logo designed from our last project

Industry/Entity Type

Physical Therapy

Contact Information for Business Card

On front
Needs our logo, contact details:
58 Wexley Lane St Clair NSW 2759
Ph/f: 02 9481 2057
info@harbourlinephysio.example.com.au

Requirements
Must have
• On the back of the card needs to have area to write down follow up appointments
• On front
• Needs our logo
• The colours have to be the colours in our logo which are: sky blue, black and white
• Font to be same as our logo please
• We want the card to look simple, not too cluttered but to the point
Should not have
• We don't need any extra pictures other than our logo

```html
<!DOCTYPE html>
<html lang="en">
<head>
<meta charset="utf-8">
<title>Harbourline Physiotherapy – Business Card</title>
<link href="https://fonts.googleapis.com/css2?family=Open+Sans:wght@400;600;700&display=swap" rel="stylesheet">
<style>
  :root {
    --stage: #e9e9ea;
    --card-dark: #151515;
    --card-light: #ffffff;
    --sky: #2f6fc4;
    --sky-soft: #4f8ad8;
    --ink-light: #e6e6e6;
    --ink-muted: #9a9a9a;
    --ink-dark: #555555;
    --rule: #8fb2e0;
  }
  * { box-sizing: border-box; margin: 0; padding: 0; }
  html, body { width: 1200px; height: 814px; overflow: hidden; }
  body {
    background: var(--stage);
    font-family: "Open Sans", Arial, sans-serif;
    position: relative;
  }
  .card {
    position: absolute;
    top: 251px;
    width: 520px;
    height: 312px;
    border-radius: 4px;
    box-shadow: 0 6px 18px rgba(0,0,0,0.18);
    overflow: hidden;
  }

  /* Front */
  .card-front { left: 60px; background: var(--card-dark); color: var(--ink-light); }
  .brand {
    position: absolute;
    left: 30px; top: 118px;
    width: 190px;
    display: flex; align-items: center; gap: 10px;
  }
  .brand-dot { width: 16px; height: 16px; border-radius: 50%; background: var(--sky); flex: none; }
  .brand-name { color: var(--sky-soft); font-weight: 700; font-size: 21px; line-height: 1.15; }
  .divider {
    position: absolute; left: 236px; top: 40px; width: 1px; height: 232px;
    background: linear-gradient(to bottom, transparent, #6a6a6a 20%, #6a6a6a 80%, transparent);
  }
  .details { position: absolute; left: 256px; top: 40px; right: 14px; font-size: 12px; line-height: 1.45; }
  .person-name { color: var(--sky-soft); font-size: 17px; font-weight: 600; line-height: 1.2; }
  .person-role { font-size: 13px; margin-bottom: 14px; }
  .address { margin-bottom: 6px; font-size: 12.5px; }
  .contact-row { display: flex; align-items: center; gap: 7px; font-size: 11.5px; }
  .contact-row svg { width: 12px; height: 12px; flex: none; fill: var(--sky-soft); }

  /* Back */
  .card-back { left: 620px; background: var(--card-light); color: var(--sky); }
  .appt-title {
    position: absolute; right: 34px; top: 30px;
    font-size: 17px; font-weight: 700; color: var(--sky);
  }
  .form-line {
    position: absolute; left: 30px; right: 30px;
    display: flex; align-items: flex-end; gap: 6px;
    font-size: 14px;
  }
  .form-line .label { flex: none; }
  .form-line .fill { flex: 1; border-bottom: 1px dotted var(--rule); height: 14px; }
  .line-time { top: 80px; left: 250px; }
  .ampm { font-size: 8px; position: absolute; right: 30px; top: 72px; }
  .line-name { top: 108px; }
  .line-date { top: 140px; }
  .days {
    position: absolute; left: 30px; right: 24px; top: 176px;
    display: flex; justify-content: space-between; font-size: 13px;
  }
  .day { display: flex; align-items: center; gap: 4px; }
  .box { width: 11px; height: 11px; border: 1px solid var(--ink-dark); }
  .line-note { top: 212px; }
  .note-extra { position: absolute; left: 80px; right: 30px; top: 246px; border-bottom: 1px dotted var(--rule); }
  .fine-print {
    position: absolute; left: 30px; right: 30px; bottom: 22px;
    font-size: 9px; color: var(--ink-dark); text-align: center; line-height: 1.4;
  }
</style>
</head>
<body>

  <section class="card card-front" aria-label="Business card front">
    <div class="brand">
      <span class="brand-dot"></span>
      <span class="brand-name">Harbourline Physiotherapy</span>
    </div>
    <div class="divider"></div>
    <div class="details">
      <p class="person-name">Daniel Harlow</p>
      <p class="person-role">CEO/Founder</p>
      <p class="address">58 Wexley Lane St Clair<br>NSW 2759</p>
      <p class="contact-row">
        <svg viewBox="0 0 24 24"><path d="M6.6 10.8a15 15 0 0 0 6.6 6.6l2.2-2.2c.3-.3.7-.4 1-.2 1.1.4 2.3.6 3.6.6.6 0 1 .4 1 1V20c0 .6-.4 1-1 1C10.6 21 3 13.4 3 4c0-.6.4-1 1-1h3.5c.6 0 1 .4 1 1 0 1.3.2 2.5.6 3.6.1.3 0 .7-.2 1z"/></svg>
        02 9481 2057
      </p>
      <p class="contact-row">
        <svg viewBox="0 0 24 24"><path d="M6 3h10v5H6zM4 9h16a1 1 0 0 1 1 1v8h-4v3H7v-3H3v-8a1 1 0 0 1 1-1zm5 7v3h6v-3z"/></svg>
        02 9481 2057
      </p>
      <p class="contact-row">
        <svg viewBox="0 0 24 24"><path d="M3 5h18v14H3zm2 2v.5l7 5 7-5V7z"/></svg>
        info@harbourlinephysio.example.com.au
      </p>
      <p class="contact-row">
        <svg viewBox="0 0 24 24"><circle cx="12" cy="12" r="9"/></svg>
        www.harbourlinephysio.example.com.au
      </p>
    </div>
  </section>

  <section class="card card-back" aria-label="Business card back">
    <h2 class="appt-title">Next Appointment</h2>
    <span class="ampm">AM/PM</span>
    <div class="form-line line-time"><span class="label">Time :</span><span class="fill"></span></div>
    <div class="form-line line-name"><span class="label">Name :</span><span class="fill"></span></div>
    <div class="form-line line-date"><span class="label">Date :</span><span class="fill"></span></div>
    <div class="days">
      <span class="day">Sun <span class="box"></span></span>
      <span class="day">Mon <span class="box"></span></span>
      <span class="day">Tue <span class="box"></span></span>
      <span class="day">Wed <span class="box"></span></span>
      <span class="day">Thu <span class="box"></span></span>
      <span class="day">Fri <span class="box"></span></span>
      <span class="day">Sat <span class="box"></span></span>
    </div>
    <div class="form-line line-note"><span class="label">Note :</span><span class="fill"></span></div>
    <div class="note-extra"></div>
    <p class="fine-print">Please give me 24 hours notice if you are unable to keep your appointment or<br>a cancellation fee may be charged.</p>
  </section>

</body>
</html>
```